Business Card Design

We would like to re-design our business cards. Our Company - Qwinrel Turbochargers, rebuilds turbochargers and sells replacement parts. Our website is: http://www.qwinrelturbochargers-example.com
We just had our logo changed. I will attach the file. Looking for fresh new/modern business card. We like the colors red, black, white and silver. Black background looks attractive, but not a requirement. The final design should communicate reasonable/competitive prices, top quality and reliability of our products.
Updates
Project Deadline Extended
Reason: Need to finalize the info on the card. Currently working on changing address and email info. Want to make sure it is the correct one before accepting the final design. Unless, this is something that can be changed at a later time..??
Industry/Entity Type
Business
Contact Information for Business Card
QWINREL TURBOCHARGERS, LLC
20473 Harwick Lane NE
Massillon, OH 44647
Tel: +1-555-214-7390
Fax: +1-555-267-1842
info@QwinrelTurbochargers-example.com
Our current business card had the following highlights:
*We rebuild all Turbocharges for Automotive, Diesel and Industrial
*Precision Balancing and in-house turbocharger needs
*All Turbocharger replacement parts are made in USA / U.K.
Look and feel
Each slider illustrates characteristics of the customer's brand and the style your logo design should communicate.

```html
<!DOCTYPE html>
<html lang="en">
<head>
<meta charset="utf-8">
<title>Qwinrel Turbochargers – Business Card</title>
<link href="https://fonts.googleapis.com/css2?family=Arimo:wght@400;700&display=swap" rel="stylesheet">
<style>
  :root {
    --backdrop: #ece7df;
    --card: #ffffff;
    --card-edge: #d8d3cb;
    --brand-red: #e42129;
    --ink: #1e1b1c;
  }
  html, body {
    margin: 0;
    padding: 0;
    overflow: hidden;
  }
  .canvas {
    position: relative;
    width: 1189px;
    height: 1200px;
    background: var(--backdrop);
    font-family: "Arimo", Arial, sans-serif;
    color: var(--ink);
  }
  .card {
    position: absolute;
    left: 171px;
    width: 856px;
    height: 490px;
    background: var(--card);
    border: 1px solid var(--card-edge);
    box-sizing: border-box;
  }
  .card--front { top: 65px; }
  .card--back { top: 625px; }

  .brand {
    position: absolute;
    left: 0;
    right: 0;
    height: 72px;
    display: flex;
    align-items: center;
    justify-content: center;
    gap: 18px;
  }
  .card--front .brand { top: 209px; }
  .card--back .brand { top: 90px; }
  .brand__mark {
    width: 72px;
    height: 72px;
    border-radius: 50%;
    background: var(--brand-red);
    flex: none;
  }
  .brand__name {
    font-size: 52px;
    font-weight: 700;
    color: var(--ink);
    letter-spacing: 0.5px;
    white-space: nowrap;
  }

  .contact {
    position: absolute;
    left: 0;
    right: 0;
    top: 240px;
    text-align: center;
  }
  .contact__name {
    margin: 0;
    font-size: 34.5px;
    font-weight: 700;
    line-height: 40px;
    color: var(--brand-red);
  }
  .contact__role {
    margin: 0;
    font-size: 23px;
    line-height: 26px;
  }
  .contact__details {
    margin: 30px 0 0;
    padding: 0;
    list-style: none;
    font-size: 22.5px;
    line-height: 29px;
  }
</style>
</head>
<body>
<main class="canvas">
  <section class="card card--front" aria-label="Card front">
    <div class="brand">
      <span class="brand__mark" aria-hidden="true"></span>
      <span class="brand__name">Qwinrel Turbochargers</span>
    </div>
  </section>

  <section class="card card--back" aria-label="Card back">
    <div class="brand">
      <span class="brand__mark" aria-hidden="true"></span>
      <span class="brand__name">Qwinrel Turbochargers</span>
    </div>
    <div class="contact">
      <p class="contact__name">Employee Name</p>
      <p class="contact__role">Managing Director</p>
      <ul class="contact__details">
        <li>555-214-7390</li>
        <li>www.qwinrelturbochargers-example.com</li>
        <li>20473 Harwick Lane NE, Dellmoor Kansas 66012</li>
      </ul>
    </div>
  </section>
</main>
</body>
</html>
```